Web and Logo Design for eCommerce site

We're launching a sister brand and require a full design for the site.

The site must have an established feel and appeal to corporate and institutional buyers.
Updates

Just a note about the wireframe design:

The Search & Rescue / Coast Guard / NVDK, etc. in the header area aren't buttons or menu items, but rather just info (along the lines of a tagline).  Sort of a "who we serve" sort of thing.

Worth noting is that it's specifically geared towards LARGE BUYERS.  For example, a police force buying 200 headlamps and 85 pairs of gloves.  So they'll register + sign in and then add a bunch of items to a RFQ.

Aim for a professional, masculine design.

Target Market(s)

We will be selling outdoor gear to the military, law enforcement, fire and rescue and first responders.

Requirements
Must have
• We require:
- Logo (vector based)

Site:
- template page
* main site template, re-skinned version of our current site
* horizontal drop-down menu
- product listings page
* thumbnail view of products
- product details page
* including elements such as product image, color/size selector, descriptions and specs (again, based loosely on our current website)
- account management page
* illustrating basic data entry styles for text box, buttons, grid, etc.

The site needs to be given a responsive design, so 2 versions of each design should be presented for desktop + mobile views.

Additional funds are available if the designer is able to fully implement the designs into a responsive framework such as bootstrap.

Nice to have
• Clean, professional design similar to:

http://military.trailvexagear.com/gov/accessories/gloves.html

http://leaf.ombrivo.com/ProductFind.aspx?language=EN&category=Hardshell&subcat=Waterproof_Jackets

```html
<!DOCTYPE html>
<html lang="en">
<head>
<meta charset="utf-8">
<title>NorthKit — Outdoor Gear for First Responders</title>
<link rel="stylesheet" href="https://fonts.googleapis.com/css2?family=Open+Sans:wght@300;400;600;700&display=swap">
<style>
:root{
  --orange:#f07a1a;
  --orange-dark:#e06a10;
  --black:#000;
  --ink:#222;
  --muted:#555;
  --line:#cfcfcf;
  --price:#e3101a;
  --star:#f6b400;
  --topbar:#efefef;
  --footer:#1e1e1e;
  --btn-grey:#7d7d7d;
}
*{box-sizing:border-box;margin:0;padding:0}
html,body{width:1200px;height:2326px;overflow:hidden;background:#fff}
body{position:relative;font-family:"Open Sans",Arial,sans-serif;color:var(--ink)}
.abs{position:absolute}

/* top bar */
.topbar{left:0;top:0;width:1200px;height:39px;background:var(--topbar)}
.lang{left:93px;top:7px;width:119px;height:24px;border-radius:12px;background:#d9d9d9;font-size:12px;display:flex;align-items:center;padding-left:13px;gap:8px;color:#333}
.lang .flag{width:16px;height:10px;background:#5a6ea8}
.lang .caret{margin-left:8px;font-size:9px}
.cart{left:843px;top:10px;font-size:14px;color:#333;display:flex;align-items:center;gap:6px}
.cart .count{color:var(--orange)}
.cart .items{color:#777}
.checkout{left:1010px;top:9px;width:97px;height:26px;background:var(--black);color:#fff;font-size:12px;display:flex;align-items:center;justify-content:center;gap:6px}

/* header */
.logo{left:91px;top:56px;width:207px;height:73px;background:#3a3a3a;border:3px solid #8a8a8a;display:flex;align-items:center;justify-content:center}
.logo span{font-size:38px;font-weight:700;color:#fff;letter-spacing:-1px}
.account{left:611px;top:64px;font-size:12px;color:#333}
.search{left:766px;top:57px;width:342px;height:33px;display:flex}
.search .field{flex:1;border:1px solid var(--line);font-size:11px;font-style:italic;color:#aaa;display:flex;align-items:center;padding-left:10px}
.search .go{width:88px;background:var(--orange);color:#fff;font-size:14px;font-weight:600;display:flex;align-items:center;justify-content:center}
.served{right:98px;top:116px;font-size:12.5px;color:var(--orange)}
.served i{font-style:normal;color:#aaa;margin:0 6px}

/* nav */
.mainnav{left:0;top:151px;width:1200px;height:47px;background:var(--black);display:flex;align-items:center;justify-content:space-between;padding:0 92px 0 91px}
.mainnav a{color:#fff;font-size:14px;text-decoration:none;text-transform:uppercase}
.mainnav a.current{color:var(--orange)}

/* hero */
.hero{left:0;top:209px;width:1200px;height:454px;background:linear-gradient(180deg,#b9b8a8 0%,#8e8f7a 30%,#4f5a3c 48%,#a8a48a 58%,#6f5c3e 80%,#4a3b28 100%)}
.hero .caption{position:absolute;left:0;top:265px;width:529px;height:137px;background:rgba(200,200,200,.6);padding:16px 0 0 65px;color:#fff;font-weight:300;font-size:34px;line-height:54px}
.hero .arrow{position:absolute;top:187px;width:38px;height:38px;border-radius:50%;background:#fff;display:flex;align-items:center;justify-content:center}

/* sidebar */
.panel{border:2px solid #d6d6d6;background:#fff}
.panel h3{font-weight:400;color:var(--orange);font-size:22px}
.shopby{left:52px;top:714px;width:268px;height:693px;padding:14px 0 0 17px}
.shopby h4{font-size:13px;font-weight:400;color:#111;margin:14px 0 8px}
.shopby ul{list-style:none;font-size:12px;color:#666;line-height:25px}
.offer{left:52px;top:1430px;width:268px;height:333px;padding:18px 0 0 20px}
.offer .photo{position:absolute;left:22px;top:78px;width:222px;height:136px;background:linear-gradient(160deg,#e9e9e9,#c9c9cf 55%,#b71c25)}
.offer .name{position:absolute;left:0;width:100%;top:252px;text-align:center;font-size:16px}
.offer .prices{position:absolute;top:284px;left:0;width:100%;text-align:center;font-size:19px}
.offer .was{text-decoration:line-through;color:#666;margin-right:34px}
.offer .now{color:var(--price)}
.newsletter{left:52px;top:1793px;width:268px;height:192px;padding:18px 0 0 20px}
.newsletter .email{margin-top:26px;width:222px;height:29px;border:1px solid #bbb;font-size:11px;font-style:italic;color:#777;display:flex;align-items:center;padding-left:8px}
.newsletter .submit{margin:22px 0 0 40px;width:133px;height:34px;background:var(--black);color:#fff;font-size:13px;display:flex;align-items:center;justify-content:center}

/* products */
.latest{left:355px;top:714px;width:793px;height:1271px;border:2px solid #d6d6d6}
.latest .bar{height:56px;background:var(--black);color:#fff;font-size:21px;display:flex;align-items:center;padding-left:22px}
.product{position:absolute;width:226px;height:347px;text-align:center}
.product.active{background:#efefef}
.product .thumb{position:absolute;left:28px;top:26px;width:170px;height:150px;border-radius:6px}
.product .name{position:absolute;top:204px;width:100%;font-size:14px;color:#444}
.product .price{position:absolute;top:229px;width:100%;font-size:19px;color:var(--price)}
.product .stars{position:absolute;top:263px;left:0;width:100%;display:flex;justify-content:center;gap:2px;color:var(--star);font-size:17px;letter-spacing:1px}
.buy{position:absolute;top:295px;left:58px;width:110px;height:31px;border-radius:16px;background:var(--btn-grey);overflow:hidden;display:flex;align-items:center;color:#fff;font-size:15px}
.buy .icon{width:50px;height:31px;background:var(--orange);border-radius:16px 0 0 16px;display:flex;align-items:center;justify-content:center;margin-right:10px;flex:none}
.dots{position:absolute;left:347px;top:1222px;display:flex;gap:9px}
.dots span{width:14px;height:14px;border-radius:50%;background:#999}
.dots span:first-child{background:#111}

/* brands */
.brands{left:50px;top:2040px;width:1100px;height:90px;display:flex;justify-content:space-between;align-items:center;padding:0 20px}
.brands span{font-size:20px;font-weight:700;color:#222;width:120px;text-align:center}

/* footer */
.footer{left:0;top:2184px;width:1200px;height:142px;background:var(--footer);color:#c8c8c8}
.footer .links{position:absolute;left:54px;top:31px;font-size:13px}
.footer .copy{position:absolute;left:54px;top:69px;font-size:13px}
.footer .follow{position:absolute;left:942px;top:24px;font-size:17px}
.footer .social{position:absolute;left:942px;top:64px;display:flex;gap:10px}
.footer .social span{width:31px;height:31px;background:#6a6a6a}
</style>
</head>
<body>

<div class="abs topbar"></div>
<div class="abs lang"><span class="flag"></span>English<span class="caret">▼</span></div>
<div class="abs cart">My Cart
  <svg width="30" height="24" viewBox="0 0 30 24"><path d="M1 3h5l4 13h14l3-9H8" fill="none" stroke="#555" stroke-width="2"/><circle cx="12" cy="20" r="2" fill="#555"/><circle cx="22" cy="20" r="2" fill="#555"/></svg>
  <span class="count">(0)</span><span class="items">Items</span></div>
<div class="abs checkout">Check Out <b>›</b></div>

<div class="abs logo"><span>NorthKit</span></div>
<div class="abs account">LOGIN &nbsp;|&nbsp; REGISTER</div>
<div class="abs search"><div class="field">Search your products</div><div class="go">Search</div></div>
<div class="abs served">Search &amp; Rescue<i>|</i>Coast Gaurd<i>|</i>NVDK<i>|</i>Fire<i>|</i>Military<i>|</i>Law Enforcement</div>

<nav class="abs mainnav">
  <a class="current" href="#">Rescue Gear</a><a href="#">Footwear</a><a href="#">Clothing</a><a href="#">Tents, Mats, Sleeping Bags</a><a href="#">Camping Gear</a><a href="#">Snow Sports</a><a href="#">Brands</a>
</nav>

<section class="abs hero" role="img" aria-label="Photo of a tent pitched by a lake with trees and mountains">
  <div class="arrow" style="left:12px"><svg width="14" height="14" viewBox="0 0 14 14"><path d="M9 2L4 7l5 5" fill="none" stroke="#000" stroke-width="2.5"/></svg></div>
  <div class="arrow" style="left:1148px"><svg width="14" height="14" viewBox="0 0 14 14"><path d="M5 2l5 5-5 5" fill="none" stroke="#000" stroke-width="2.5"/></svg></div>
  <div class="caption">Great outdoor Gear for<br>Canada's First Responders</div>
</section>

<aside class="abs panel shopby">
  <h3>Shop By</h3>
  <h4>CATEGORY</h4>
  <ul><li>Mitts</li><li>Liners</li><li>Touchscree</li><li>liners</li><li>Mitts</li></ul>
  <h4 style="margin-top:18px">PRODUCT HIGHLIGHTS</h4>
  <ul><li>Rescue gear</li><li>Footwear</li><li>Clothing</li><li>Tents, mats, sleeping bags</li><li>Camping gear</li><li>Snow sports</li><li>Brands</li></ul>
  <h4 style="margin-top:18px">SIZE</h4>
  <ul><li>XS (4)</li><li>S (40)</li><li>M (40)</li><li>L (40)</li><li>XL (39)</li><li>XXL (33)</li><li>S/M (1)</li><li>L/XL (1)</li></ul>
</aside>

<aside class="abs panel offer">
  <h3>Current Offer</h3>
  <div class="photo" role="img" aria-label="Product photo of a dome tent with camp chairs and sleeping bag"></div>
  <div class="name">Latest Rescue Gear</div>
  <div class="prices"><span class="was">£179.99</span><span class="now">$109.99</span></div>
</aside>

<aside class="abs panel newsletter">
  <h3>Newsletter Sign Up</h3>
  <div class="email">Enter your Email ID</div>
  <div class="submit">SUBMIT</div>
</aside>

<svg width="0" height="0" style="position:absolute">
  <defs>
    <symbol id="cart-icon" viewBox="0 0 22 18">
      <path d="M1 2h4l3 10h10l2.5-7H6" fill="none" stroke="#fff" stroke-width="2" stroke-linejoin="round"/>
      <path d="M8 7.5h11M9 10h9" stroke="#fff" stroke-width="1.3"/>
      <circle cx="9" cy="15.5" r="1.6" fill="#fff"/><circle cx="17" cy="15.5" r="1.6" fill="#fff"/>
    </symbol>
  </defs>
</svg>

<main class="abs latest">
  <div class="bar">Latest Products</div>

  <div class="product active" style="left:28px;top:92px"><div class="thumb" role="img" aria-label="Hiking boot" style="background:linear-gradient(135deg,#6a3a2a,#2b2b2b)"></div><div class="name">Rescue Gear Latest</div><div class="price">$119.99</div><div class="stars">★★★★★</div><div class="buy"><span class="icon"><svg width="22" height="18"><use href="#cart-icon"/></svg></span>BUY</div></div>
  <div class="product" style="left:279px;top:92px"><div class="thumb" role="img" aria-label="Dome tent" style="background:linear-gradient(160deg,#e8e2c8,#3c4f9a 60%,#8cb04a)"></div><div class="name">Rescue Gear Latest</div><div class="price">$119.99</div><div class="stars">★★★★★</div><div class="buy"><span class="icon"><svg width="22" height="18"><use href="#cart-icon"/></svg></span>BUY</div></div>
  <div class="product" style="left:535px;top:92px"><div class="thumb" role="img" aria-label="Blue dome tent" style="background:linear-gradient(160deg,#b9c9d6,#2f9bc6)"></div><div class="name">Rescue Gear Latest</div><div class="price">$119.99</div><div class="stars">★★★★★</div><div class="buy"><span class="icon"><svg width="22" height="18"><use href="#cart-icon"/></svg></span>BUY</div></div>

  <div class="product" style="left:28px;top:466px"><div class="thumb" role="img" aria-label="Red t-shirt" style="background:linear-gradient(160deg,#d8333a,#a81a20)"></div><div class="name">Rescue Gear Latest</div><div class="price">$119.99</div><div class="stars">★★★★★</div><div class="buy"><span class="icon"><svg width="22" height="18"><use href="#cart-icon"/></svg></span>BUY</div></div>
  <div class="product" style="left:279px;top:466px"><div class="thumb" role="img" aria-label="Purple shorts" style="background:linear-gradient(160deg,#4a1e3c,#2a1024)"></div><div class="name">Rescue Gear Latest</div><div class="price">$119.99</div><div class="stars">★★★★★</div><div class="buy"><span class="icon"><svg width="22" height="18"><use href="#cart-icon"/></svg></span>BUY</div></div>
  <div class="product" style="left:535px;top:466px"><div class="thumb" role="img" aria-label="Dark tank top" style="background:linear-gradient(160deg,#3a1a34,#1c0c1a)"></div><div class="name">Rescue Gear Latest</div><div class="price">$119.99</div><div class="stars">★★★★★</div><div class="buy"><span class="icon"><svg width="22" height="18"><use href="#cart-icon"/></svg></span>BUY</div></div>

  <div class="product" style="left:28px;top:843px"><div class="thumb" role="img" aria-label="Green dome tent" style="background:linear-gradient(160deg,#6b7a3a,#2a2f22)"></div><div class="name">Rescue Gear Latest</div><div class="price">$119.99</div><div class="stars">★★★★★</div><div class="buy"><span class="icon"><svg width="22" height="18"><use href="#cart-icon"/></svg></span>BUY</div></div>
  <div class="product" style="left:279px;top:843px"><div class="thumb" role="img" aria-label="Black leather work boot" style="background:linear-gradient(160deg,#3a2a22,#111)"></div><div class="name">Rescue Gear Latest</div><div class="price">$119.99</div><div class="stars">★★★★★</div><div class="buy"><span class="icon"><svg width="22" height="18"><use href="#cart-icon"/></svg></span>BUY</div></div>
  <div class="product" style="left:535px;top:843px"><div class="thumb" role="img" aria-label="Hiking boot" style="background:linear-gradient(135deg,#6a3a2a,#2b2b2b)"></div><div class="name">Rescue Gear Latest</div><div class="price">$119.99</div><div class="stars">★★★★★</div><div class="buy"><span class="icon"><svg width="22" height="18"><use href="#cart-icon"/></svg></span>BUY</div></div>

  <div class="dots"><span></span><span></span><span></span><span></span><span></span></div>
</main>

<section class="abs brands">
  <span>Harbek</span><span>Ombrivo</span><span>Talvo</span><span>Kesta</span><span>Trailmeal</span><span>Graniq</span><span>Weldale</span>
</section>

<footer class="abs footer">
  <div class="links">Terms and Conditions | Privacy Policy | &nbsp;Contact | Sitemap</div>
  <div class="copy">All Rights reserved. Copyrights @ 2013</div>
  <div class="follow">Follow Us on</div>
  <div class="social"><span></span><span></span><span></span><span></span><span></span></div>
</footer>

</body>
</html>
```